Australian Trucking Company Requires Professional Looking Stationary

We require a professional looking stationary design that incorporates our newly designed logo.

Our business, called "Brell Haulage Contracting", provides contracting work, transport and logistics to business in Western Australia particularly with links to the mining sector.

We are a small business looking to expand and our new logo and our new stationary will help develop our brand image in our market place.

Target Market(s)

Businesses and Corporation with links to the Mining Sector

Industry/Entity Type

Small Business

Requirements
Must have
• The letterhead must have the following details:
The new logo

Text saying: "Brell Holdings Pty Ltd (ACN 582 316 907) ATF The Brell Discretionary Trust T/AS"
"ABN 71 834 209 553"
Address "P.O Box 817 Wattlegrove WA, 6958"
Phone: 08 9352 7140
Email: brellhaul@mailbox-example.com.au

The text on the letterhead should be editable as the details are likely to change in the near future. Provision should be made for a website address all though one isn't available at the moment.

The styling, layout and font text is entirely up to the designer.

```html
<!DOCTYPE html>
<html lang="en">
<head>
<meta charset="utf-8">
<title>Brell Haulage Contracting – Letterhead Options</title>
<link href="https://fonts.googleapis.com/css2?family=Open+Sans:wght@400;600;800&display=swap" rel="stylesheet">
<style>
  :root {
    --backdrop: #e8e2d8;
    --paper: #ffffff;
    --brand-red: #c8102e;
    --brand-red-dark: #7d0a1c;
    --silver: #b9bcc0;
    --ink: #3a3a3a;
    --ink-soft: #7a7a7a;
    --rule: #9a9a9a;
  }
  * { box-sizing: border-box; margin: 0; padding: 0; }
  html, body { width: 1200px; height: 449px; overflow: hidden; }
  body {
    position: relative;
    background: var(--backdrop);
    font-family: "Open Sans", Arial, sans-serif;
    color: var(--ink);
  }
  .sheet {
    position: absolute;
    top: 40px;
    width: 253px;
    height: 355px;
    background: var(--paper);
    box-shadow: 0 1px 3px rgba(0,0,0,.25);
    overflow: hidden;
  }
  .sheet--plain { left: 42px; }
  .sheet--footer-band { left: 336px; }
  .sheet--header-band { left: 629px; }
  .sheet--fax { left: 923px; }

  .caption {
    position: absolute;
    top: 399px;
    width: 253px;
    text-align: center;
    font-size: 7px;
    color: var(--ink-soft);
  }

  .brand {
    position: absolute;
    display: flex;
    align-items: center;
    gap: 5px;
  }
  .brand__square {
    width: 26px;
    height: 22px;
    background: var(--silver);
  }
  .brand__name {
    font-weight: 800;
    font-size: 8.5px;
    line-height: 8.5px;
    color: var(--brand-red);
    text-transform: uppercase;
    letter-spacing: .2px;
  }
  .brand--top { top: 10px; left: 68px; }
  .brand--header { top: 36px; left: 132px; }

  .fine {
    position: absolute;
    left: 0; right: 0;
    text-align: center;
    font-size: 3.6px;
    line-height: 5px;
    color: var(--ink-soft);
  }
  .fine--red { color: var(--brand-red); }
  .fine--white { color: #fff; }
  .fine--right { left: auto; right: 10px; text-align: right; }

  .contact-row {
    position: absolute;
    left: 0; right: 0;
    display: flex;
    justify-content: center;
    gap: 10px;
    font-size: 3.8px;
    color: var(--ink);
  }
  .contact-row span::before {
    content: "";
    display: inline-block;
    width: 3px; height: 3px;
    margin-right: 2px;
    background: var(--brand-red);
    vertical-align: middle;
  }

  /* Colour band areas (decorative wave zones shown as plain gradient fields) */
  .band {
    position: absolute;
    left: 0;
    width: 253px;
    background: linear-gradient(90deg, var(--brand-red-dark), var(--brand-red) 60%, var(--brand-red-dark));
  }
  .band--bottom { bottom: 0; height: 60px; }
  .band--top { top: 0; height: 32px; }

  .contact-stack {
    position: absolute;
    font-size: 3.8px;
    line-height: 6px;
    color: #fff;
  }
  .contact-stack li { list-style: none; }
  .contact-stack--right { right: 10px; text-align: right; }
  .contact-stack--right li::after {
    content: ""; display: inline-block; width: 3px; height: 3px;
    margin-left: 3px; background: #fff; vertical-align: middle;
  }
  .contact-stack--left { left: 10px; top: 5px; }
  .contact-stack--left li::before {
    content: ""; display: inline-block; width: 3px; height: 3px;
    margin-right: 3px; background: #fff; vertical-align: middle;
  }

  .fax-title {
    position: absolute; top: 98px; left: 17px;
    font-size: 15px; font-weight: 400; color: var(--ink);
  }
  .fax-fields {
    position: absolute; top: 127px; left: 17px; right: 17px;
    display: grid; grid-template-columns: 1fr 1fr; column-gap: 10px; row-gap: 8px;
  }
  .fax-field {
    border-bottom: .6px solid var(--rule);
    font-size: 3.6px; color: var(--ink-soft); height: 7px;
  }
  .fax-options {
    position: absolute; top: 191px; left: 17px; right: 17px;
    display: flex; justify-content: space-between;
    font-size: 3.6px; color: var(--ink-soft);
  }
  .fax-options span::before {
    content: ""; display: inline-block; width: 5px; height: 5px;
    border: .6px solid var(--rule); margin-right: 2px; vertical-align: middle;
  }
</style>
</head>
<body>

<section class="sheet sheet--plain">
  <div class="brand brand--top">
    <div class="brand__square"></div>
    <div class="brand__name">Brell<br>Haulage<br>Contracting</div>
  </div>
  <div class="contact-row" style="top:322px"><span>P.O Box 817 Wattlegrove WA, 6958</span></div>
  <div class="contact-row" style="top:331px">
    <span>08 9352 7140</span><span>brellhaul@mailbox-example.com.au</span><span>www.brellhaulage-example.com.au</span>
  </div>
  <p class="fine" style="top:340px">Brell Holdings Pty Ltd (ACN 582 316 907) ATF The Brell Discretionary Trust T/AS &nbsp;|&nbsp; ABN 71 834 209 553</p>
</section>
<p class="caption" style="left:42px">Option 1</p>

<section class="sheet sheet--footer-band">
  <div class="brand brand--top">
    <div class="brand__square"></div>
    <div class="brand__name">Brell<br>Haulage<br>Contracting</div>
  </div>
  <div class="band band--bottom" role="img" aria-label="Decorative red and silver wave band"></div>
  <ul class="contact-stack contact-stack--right" style="top:300px">
    <li>08 9352 7140</li>
    <li>brellhaul@mailbox-example.com.au</li>
    <li>www.brellhaulage-example.com.au</li>
    <li>P.O Box 817 Wattlegrove WA, 6958</li>
  </ul>
  <p class="fine fine--white fine--right" style="top:331px">ABN 71 834 209 553</p>
  <p class="fine fine--white" style="top:343px">Brell Holdings Pty Ltd (ACN 582 316 907) ATF The Brell Discretionary Trust T/AS</p>
</section>
<p class="caption" style="left:336px">Option 2</p>

<section class="sheet sheet--header-band">
  <div class="band band--top" role="img" aria-label="Decorative red and silver wave band"></div>
  <ul class="contact-stack contact-stack--left">
    <li>P.O Box 817 Wattlegrove WA, 6958</li>
    <li>08 9352 7140</li>
    <li>brellhaul@mailbox-example.com.au</li>
    <li>www.brellhaulage-example.com.au</li>
  </ul>
  <div class="brand brand--header">
    <div class="brand__square"></div>
    <div class="brand__name">Brell<br>Haulage<br>Contracting</div>
  </div>
  <p class="fine" style="top:334px">ABN 71 834 209 553</p>
  <p class="fine fine--red" style="top:343px">Brell Holdings Pty Ltd (ACN 582 316 907) ATF The Brell Discretionary Trust T/AS</p>
</section>
<p class="caption" style="left:629px">Option 3</p>

<section class="sheet sheet--fax">
  <div class="brand brand--top">
    <div class="brand__square"></div>
    <div class="brand__name">Brell<br>Haulage<br>Contracting</div>
  </div>
  <p class="fine fine--red" style="top:42px">Brell Holdings Pty Ltd (ACN 582 316 907) ATF The Brell Discretionary Trust T/AS</p>
  <h1 class="fax-title">FAX</h1>
  <div class="fax-fields">
    <div class="fax-field">To:</div><div class="fax-field">From:</div>
    <div class="fax-field">Fax:</div><div class="fax-field">Pages:</div>
    <div class="fax-field">Phone:</div><div class="fax-field">Date:</div>
    <div class="fax-field">Re:</div><div class="fax-field">CC:</div>
  </div>
  <div class="fax-options">
    <span>Urgent</span><span>For Review</span><span>Please Comment</span><span>Please Reply</span><span>Please Recycle</span>
  </div>
  <div class="band band--bottom" role="img" aria-label="Decorative red and silver wave band"></div>
  <p class="fine fine--white fine--right" style="top:301px">ABN 71 834 209 553</p>
  <ul class="contact-stack contact-stack--right" style="top:310px">
    <li>08 9352 7140</li>
    <li>brellhaul@mailbox-example.com.au</li>
    <li>www.brellhaulage-example.com.au</li>
    <li>P.O Box 817 Wattlegrove WA, 6958</li>
  </ul>
</section>
<p class="caption" style="left:923px">Option 4</p>

</body>
</html>
```